Podiatry clinic requires a modern revamp and editing of existing website.

I would like a fresh new look and updated information for my current business website. An easy to navigate site with prominent address and phone number for call to action. We are a podiatry clinic that focuses on general and sports podiatry.
I would like 4 pages; including Home page, About Us, Services & Contact.
www.brambleridgepodiatry.net

Target Market(s)

Active working professionals.

Industry/Entity Type

Medical

Coding

Coded - Design and coding required

Number of Pages Required

4 page

Font styles to use
Sans Serif

Colors
6b449b

Requirements
Must have
• A modern look with logo and active images; clean and uncluttered. Visible phone number and address for call to action.
• 4 pages - Home, About Us, Services, Contact.
• Home page - update address & service logos.
• About Us - update of personal information.
• Services - Revamp of existing page.
• Contact page to include Google map, email & phone number.
Nice to have
• Ability to add content easily; eg. a blog or adding video onto Home page.
• Link to Facebook page.

```html
<!DOCTYPE html>
<html lang="en">
<head>
<meta charset="utf-8">
<title>Contact – Bramble Ridge Podiatry</title>
<link rel="stylesheet" href="https://fonts.googleapis.com/css2?family=Open+Sans:wght@400;700&family=Raleway:wght@300;400;500&family=Roboto+Condensed:wght@300;400;700&display=swap">
<style>
  :root {
    --brand-purple: #6b449b;
    --header-top: #6e58c6;
    --header-bottom: #f3f1fa;
    --nav-bg: #46329a;
    --nav-active: #79bd2a;
    --footer-bg: #5a3db4;
    --white: #ffffff;
    --field-text: #8c8c8c;
    --hero-dark: #3b4031;
    --hero-mid: #5f6b49;
    --hero-light: #8e9a78;
    --map-fill: #ebe8e2;
    --map-road: #f8f7f3;
  }
  * { box-sizing: border-box; margin: 0; padding: 0; }
  html, body { width: 1200px; height: 842px; overflow: hidden; }
  body { position: relative; font-family: "Open Sans", sans-serif; background: var(--white); }

  .site-header {
    position: absolute; left: 0; top: 0; width: 1200px; height: 175px;
    background: linear-gradient(to bottom, var(--header-top) 0%, #a294db 45%, var(--header-bottom) 100%);
  }
  .brand {
    position: absolute; left: 77px; top: 62px;
    display: flex; align-items: center; gap: 12px;
    font-family: "Roboto Condensed", sans-serif; font-weight: 700;
    font-size: 30px; color: var(--white); letter-spacing: 0.2px;
  }
  .brand-dot { width: 34px; height: 34px; border-radius: 50%; background: var(--nav-bg); }
  .header-info {
    position: absolute; right: 85px; top: 42px; text-align: right;
    font-family: "Roboto Condensed", sans-serif; font-weight: 300; color: var(--white);
  }
  .header-info .line { display: flex; align-items: center; justify-content: flex-end; gap: 8px; font-size: 21px; height: 32px; }
  .header-info .line + .line { margin-top: 15px; }
  .header-info strong { font-weight: 400; }

  .main-nav {
    position: absolute; left: 0; top: 175px; width: 1200px; height: 63px;
    background: var(--nav-bg); font-family: "Raleway", sans-serif; font-size: 18px;
  }
  .main-nav a {
    position: absolute; top: 0; height: 63px; line-height: 63px;
    color: var(--white); text-decoration: none;
  }
  .main-nav a.active { background: var(--nav-active); padding: 0 33px; left: 77px; }

  .hero {
    position: absolute; left: 0; top: 238px; width: 1200px; height: 551px;
    background:
      radial-gradient(ellipse at 50% 10%, rgba(180,190,160,0.55), transparent 60%),
      linear-gradient(to bottom, var(--hero-light) 0%, var(--hero-mid) 35%, var(--hero-dark) 100%);
  }
  .hero-title {
    position: absolute; left: 0; top: 48px; width: 1200px; text-align: center;
    font-family: "Raleway", sans-serif; font-weight: 300; font-size: 41px; color: var(--white);
  }
  .contact-form .field {
    position: absolute; left: 77px; width: 437px; height: 51px;
    background: var(--white); border-radius: 4px;
    font-family: Arial, sans-serif; font-size: 14px; color: var(--field-text);
    padding: 17px 17px;
  }
  .submit-btn {
    position: absolute; left: 77px; top: 448px; width: 166px; height: 51px;
    background: var(--brand-purple); border-radius: 26px; color: var(--white);
    font-family: "Raleway", sans-serif; font-weight: 500; font-size: 23px;
    display: flex; align-items: center; justify-content: center; letter-spacing: 0.5px;
  }
  .map-area {
    position: absolute; left: 535px; top: 157px; width: 276px; height: 275px;
    background: linear-gradient(135deg, var(--map-road) 0%, var(--map-fill) 60%, #e1ddd4 100%);
    border: 1px solid var(--white);
  }
  .contact-address { position: absolute; left: 855px; top: 155px; width: 300px; height: 260px; color: var(--white); }
  .contact-address h2 { font-family: "Raleway", sans-serif; font-weight: 400; font-size: 20px; margin-bottom: 18px; }
  .contact-item { position: absolute; left: 0; display: flex; gap: 12px; font-size: 15px; line-height: 23px; white-space: nowrap; }
  .contact-item svg { flex: none; }
  .contact-item strong { font-weight: 700; }
  .social-circle {
    position: absolute; left: -4px; top: 201px; width: 46px; height: 46px;
    border-radius: 50%; background: var(--white);
  }
  .site-footer {
    position: absolute; left: 0; top: 789px; width: 1200px; height: 53px;
    background: var(--footer-bg); color: var(--white); text-align: center;
    font-size: 15px; line-height: 53px;
  }
</style>
</head>
<body>
  <header class="site-header">
    <div class="brand"><span class="brand-dot"></span>Bramble Ridge Podiatry</div>
    <div class="header-info">
      <div class="line">
        <svg width="17" height="26" viewBox="0 0 17 26"><path d="M8.5 0C3.8 0 0 3.8 0 8.5 0 14.5 8.5 26 8.5 26S17 14.5 17 8.5C17 3.8 13.2 0 8.5 0zm0 12a3.5 3.5 0 1 1 0-7 3.5 3.5 0 0 1 0 7z" fill="#fff"/></svg>
        Suite 208 / 72 Hawthorn Lane Kelmore 3141
      </div>
      <div class="line">
        <svg width="30" height="30" viewBox="0 0 30 30"><path d="M7 3l5 6-3 3c1.5 3.5 4.5 6.5 8 8l3-3 6 5-3 4C13 26 4 17 3 7z" fill="#fff"/></svg>
        CALL US NOW : <strong>1300 482 907</strong>
      </div>
    </div>
  </header>

  <nav class="main-nav">
    <a class="active" href="#">HOME</a>
    <a href="#" style="left:234px">ABOUT</a>
    <a href="#" style="left:374px">SERVICES</a>
    <a href="#" style="left:538px">CONTACT</a>
  </nav>

  <main class="hero" role="img" aria-label="Photograph of a runner jogging along a country road at sunset">
    <h1 class="hero-title">CONTACT US</h1>

    <div class="contact-form">
      <div class="field" style="top:156px">Name</div>
      <div class="field" style="top:213px">E-Mail</div>
      <div class="field" style="top:270px">Phone</div>
      <div class="field" style="top:328px;height:103px">Message</div>
      <div class="submit-btn">SUBMIT</div>
    </div>

    <div class="map-area" role="img" aria-label="Street map showing the clinic location"></div>

    <section class="contact-address">
      <h2>CONTACT ADDRESS</h2>
      <div class="contact-item" style="top:44px">
        <svg width="22" height="32" viewBox="0 0 22 32"><path d="M11 1.5C5.8 1.5 1.5 5.8 1.5 11 1.5 18 11 30 11 30s9.5-12 9.5-19c0-5.2-4.3-9.5-9.5-9.5z" fill="none" stroke="#fff" stroke-width="1.6"/><circle cx="11" cy="11" r="4" fill="none" stroke="#fff" stroke-width="1.6"/></svg>
        <span>Suite 208 / 72 Hawthorn Lane<br>Kelmore 3141.</span>
      </div>
      <div class="contact-item" style="top:106px">
        <svg width="22" height="22" viewBox="0 0 22 22"><path d="M5 1.5l4 4.5-2 2.5c1.2 2.7 3.3 4.8 6 6l2.5-2 4.5 4-2.5 3.5C9 19.5 2.5 13 1.5 4z" fill="none" stroke="#fff" stroke-width="1.5"/></svg>
        <strong>1300 482 907</strong>
      </div>
      <div class="contact-item" style="top:148px">
        <svg width="22" height="22" viewBox="0 0 22 22"><rect x="1.5" y="4.5" width="19" height="13" rx="1.5" fill="none" stroke="#fff" stroke-width="1.6"/><path d="M2 5.5l9 7 9-7" fill="none" stroke="#fff" stroke-width="1.6"/></svg>
        <span>info@brambleridgepodiatry.net</span>
      </div>
      <a class="social-circle" href="#" aria-label="Social page"></a>
    </section>
  </main>

  <footer class="site-footer">© Bramble Ridge Podiatry- 2016. All Rights Reserved.</footer>
</body>
</html>
```